New Business Card for Web Design/Internet Marketing Company

Looking for a great looking new business card. We are a 10 year old web design, internet marketing and website management company that works mostly with small businesses.

Our new card needs to better match the colors and style of our website, be bold, extremely usable and slightly edgy.

Target Market(s)

Small/Medium businesses that have websites

Industry/Entity Type

Internet

Requirements
Must have
• Front and back design, full color, rounded corners please

Must use the colors/style of our website (JPG provided)

INFO FOR CARDS (as readable as possible please)
Mark Lenner
President/CEO
mark@trelvanmedia.example
Phone: 520-381-7459
Toll Free: 866-381-7459
Address: 4315 W. Calloway Ave. Ste. 140, Tucson, AZ 85792

THINGS I WANT TO PROMOTE (if there is room):
1. Our Website - www.trelvanmedia.example

2. Social Media
Twitter: @trelvanmedia
Facebook: www.facebook.com/trelvanmedia

3. Our Services
Web Design
Internet Marketing
Website Management

```html
<!DOCTYPE html>
<html lang="en">
<head>
<meta charset="utf-8">
<title>Trelvan Media – Business Card</title>
<link rel="stylesheet" href="https://fonts.googleapis.com/css2?family=Source+Sans+3:wght@400;600;700&display=swap">
<style>
  :root {
    --brand-blue: #1a93c9;
    --brand-orange: #ef8a2e;
    --ink-grey: #5a5a5a;
    --paper: #ffffff;
    --stage: #ececec;
  }
  * { box-sizing: border-box; margin: 0; padding: 0; }
  html, body { width: 1200px; height: 758px; overflow: hidden; }
  body {
    background: var(--stage);
    font-family: "Source Sans 3", "Myriad Pro", Arial, sans-serif;
    position: relative;
  }
  .card {
    position: absolute;
    top: 224px;
    width: 540px;
    height: 310px;
    border-radius: 26px;
    overflow: hidden;
    box-shadow: 0 6px 18px rgba(0,0,0,0.18);
  }

  /* Front */
  .card-front { left: 40px; background: var(--paper); }
  .front-brand {
    position: absolute; top: 42px; left: 0; right: 0;
    display: flex; justify-content: center; align-items: center; gap: 10px;
  }
  .brand-dot { width: 22px; height: 22px; border-radius: 50%; background: var(--brand-orange); }
  .brand-name { font-size: 38px; font-weight: 700; color: var(--brand-blue); letter-spacing: -0.5px; }
  .rule { position: absolute; left: 0; right: 0; height: 2px; background: var(--brand-orange); }
  .rule-top { top: 134px; }
  .rule-mid { top: 226px; }
  .rule-bottom { top: 282px; }
  .contact-band {
    position: absolute; top: 142px; left: 0; right: 0; height: 78px;
    background: var(--brand-blue); color: var(--paper);
    display: flex; align-items: center;
  }
  .address {
    width: 290px; text-align: right; padding-right: 16px;
    font-size: 14px; line-height: 1.3;
  }
  .band-divider { width: 1px; height: 62px; background: rgba(255,255,255,0.7); }
  .contact-list { list-style: none; padding-left: 10px; font-size: 13.5px; line-height: 1.3; }
  .contact-list li { display: flex; align-items: center; gap: 6px; }
  .contact-list svg { width: 11px; height: 11px; flex: none; }
  .signature {
    position: absolute; top: 236px; left: 0; right: 0; text-align: center;
    font-size: 21px; color: var(--ink-grey);
  }
  .signature .person { color: var(--brand-orange); font-weight: 700; }

  /* Back */
  .card-back {
    left: 620px; background: var(--brand-blue); color: var(--paper);
    text-align: center;
  }
  .back-brand {
    position: absolute; top: 58px; left: 0; right: 0;
    display: flex; justify-content: center; align-items: center; gap: 12px;
  }
  .back-brand .brand-dot { width: 30px; height: 30px; background: var(--paper); }
  .back-brand .brand-name { font-size: 54px; color: var(--paper); }
  .services-title { position: absolute; top: 150px; left: 0; right: 0; font-size: 27px; font-weight: 700; }
  .services-list { position: absolute; top: 186px; left: 0; right: 0; font-size: 22px; line-height: 1.15; }
  .social {
    position: absolute; top: 258px; left: 0; right: 0;
    display: flex; justify-content: center; gap: 34px; font-size: 14px;
  }
  .social span { display: flex; align-items: center; gap: 6px; }
  .social-mark { width: 12px; height: 12px; background: var(--paper); opacity: 0.85; border-radius: 2px; }
</style>
</head>
<body>

<section class="card card-front" aria-label="Card front">
  <div class="front-brand">
    <span class="brand-dot"></span>
    <span class="brand-name">Trelvan Media</span>
  </div>
  <div class="rule rule-top"></div>
  <div class="contact-band">
    <div class="address">4315 W. Calloway Ave. Ste. 140<br>Tucson, AZ 85792</div>
    <div class="band-divider"></div>
    <ul class="contact-list">
      <li><svg viewBox="0 0 12 12"><circle cx="6" cy="6" r="5.3" fill="none" stroke="#fff"/><path d="M4 3.2l1 1.4-.6.8c.4.9 1.1 1.6 2 2l.8-.6 1.4 1-.5 1c-2.4-.3-4.3-2.2-4.6-4.6z" fill="#fff"/></svg>866-381-7459</li>
      <li><svg viewBox="0 0 12 12"><circle cx="6" cy="6" r="5.3" fill="none" stroke="#fff"/><path d="M4 3.2l1 1.4-.6.8c.4.9 1.1 1.6 2 2l.8-.6 1.4 1-.5 1c-2.4-.3-4.3-2.2-4.6-4.6z" fill="#fff"/></svg>520-381-7459</li>
      <li><svg viewBox="0 0 12 12"><circle cx="6" cy="6" r="6" fill="#fff"/><rect x="3" y="4" width="6" height="4.2" fill="none" stroke="#1a93c9" stroke-width="0.9"/><path d="M3 4l3 2.4L9 4" fill="none" stroke="#1a93c9" stroke-width="0.9"/></svg>mark@trelvanmedia.example</li>
      <li><svg viewBox="0 0 12 12"><circle cx="6" cy="6" r="6" fill="#fff"/><path d="M0.5 6h11M6 .5c-2.4 3-2.4 8 0 11M6 .5c2.4 3 2.4 8 0 11" fill="none" stroke="#1a93c9" stroke-width="0.8"/></svg>www.trelvanmedia.example</li>
    </ul>
  </div>
  <div class="rule rule-mid"></div>
  <p class="signature"><span class="person">Mark Lenner,</span> President/CEO</p>
  <div class="rule rule-bottom"></div>
</section>

<section class="card card-back" aria-label="Card back">
  <div class="back-brand">
    <span class="brand-dot"></span>
    <span class="brand-name">Trelvan Media</span>
  </div>
  <h2 class="services-title">Our Services</h2>
  <p class="services-list">• Web Design • Internet Marketing<br>• Website Management</p>
  <div class="social">
    <span><i class="social-mark"></i>@trelvanmedia</span>
    <span><i class="social-mark"></i>trelvanmedia</span>
  </div>
</section>

</body>
</html>
```